Web Design For Marlow Pool Service

We are working with a company that wants a website for their pool service. Some sites to use for content/competitors and inspiration:
https://sacramento.brightwaterpoolco.example/builder/newbuild/repair/ppc
https://hollowbrookpoolcareplus.example/
https://lakemontpoolservice.example/
https://www.dravenspoolresurfacing.example/pool-renovation-ga/
Thank you for taking the time to consider designing a website for us. We are web developers based in Stockton, CA, USA. Most of our projects go through the same process. Understanding this process may help you win a project with us. We custom-code all of our websites in-house. We don’t have any requirements as to what tools you use for your design, but we prefer Figma files. For any design that we label as four-stars, we send it to the client for review. The client picks the final design they want us to use. Once we complete this process, we will continue to show additional clients all the four-star sites and purchase them later. Your designs will have multiple chances to sell. For better chances of success, we ask that you follow these guidelines.
IMAGES:
If you use any images or icons in the design, we ask that you have a link to the asset so we can purchase the image/icon. Most of the designs we submit do not have the customer’s images on them unless they have some great images. Be creative; show us the feeling you are trying to portray with your image choices. Use any royalty-free site you choose. We subscribe to Adobe and mainly use their images, but we can purchase images outside of Adobe. PLEASE NOTE: we will not submit designs to clients with watermarks on the images.
FONTS:
We ask that you identify the fonts used in the design. This can be done in a message if you want. We typically use Google Fonts and Adobe Fonts.
CONTENT:
We're always open to different content and ideas. We often submit designs with stock images so the client can see our vision. We typically take pictures after the website launch to use their images with our vision. Lorem Ipsum is fine for paragraphs, but we ask that you write the headers in correct English. We want to be able to show the vision and identify the sections of the website.
INSPIRATION:
We typically add a couple of links in the brief of websites we like to help you get started in your design.
REVISIONS:
We do not often ask for revisions of the designs unless we see something in the design that may not appeal to the client. If there are slight changes that we want to make, we do that in the development process.
FEEDBACK:
We rarely give feedback on designs during the design process. We are working on many website projects and do not have the time to provide feedback. We usually respond if your request is well thought out and asks specific questions, but a note asking “feedback, please” usually goes unanswered.
Number of Pages Required
1 page
Look and feel
Each slider illustrates characteristics of the customer's brand and the style your logo design should communicate.

```html
<!DOCTYPE html>
<html lang="en">
<head>
<meta charset="utf-8">
<title>Marlow Pool Service</title>
<link rel="stylesheet" href="https://fonts.googleapis.com/css2?family=Libre+Baskerville:wght@400;700&family=Lato:wght@400;700;900&family=Tinos&display=swap">
<style>
:root{
  --navy:#1b3f73;
  --blue:#2a9bf0;
  --grey:#efefef;
  --grey-light:#f3f3f3;
  --ink:#3a3a3a;
  --footer:#23233a;
  --white:#fff;
}
*{margin:0;padding:0;box-sizing:border-box}
html,body{width:1200px;height:4748px;overflow:hidden;background:var(--white)}
body{position:relative;font-family:"Lato",sans-serif;color:var(--ink)}
.abs{position:absolute}
.heading{font-family:"Libre Baskerville",serif;font-weight:700;color:var(--navy);line-height:1.2}
.eyebrow{font-size:9px;font-weight:900;letter-spacing:.3px;text-transform:uppercase;color:#222}
.rule{height:2px;width:30px;background:var(--blue)}
.copy{font-size:11.5px;line-height:1.55;color:#555}
.btn{display:flex;align-items:center;justify-content:center;background:var(--blue);color:var(--white);font-size:9px;font-weight:900;letter-spacing:.4px;text-transform:uppercase}
.photo{display:block}

/* hero */
.hero-bg{left:0;top:0;width:1015px;height:656px;background:var(--grey)}
.nav{top:38px;left:0;width:1200px;height:20px;font-size:13px;color:#333;letter-spacing:.3px}
.nav span{position:absolute;top:0}
.brand{display:flex;flex-direction:column;color:var(--navy);font-family:"Libre Baskerville",serif;font-weight:400;line-height:1}
.brand .big{font-size:34px;letter-spacing:1px}
.brand .small{font-size:16px;letter-spacing:3.4px;margin-top:4px}
.hero-title{left:140px;top:204px;font-size:52px;line-height:61px}
.hero-copy{left:140px;top:400px;width:330px}
.hero-btn{left:140px;top:463px;width:136px;height:51px}
.hero-photo{left:592px;top:74px;width:571px;height:516px;background:linear-gradient(135deg,#c9b49a 0%,#8d7a68 35%,#4fa9b8 70%,#2f7e92 100%)}

/* about */
.about-photo{left:142px;top:761px;width:365px;height:384px;background:linear-gradient(160deg,#2e88c6 0%,#9aa7b1 40%,#5a5f66 70%,#b98a5a 100%)}
.call-box{left:219px;top:1062px;width:365px;height:149px;background:var(--navy);color:var(--white);display:flex;align-items:center;padding-left:58px;gap:22px}
.call-box .lbl{font-family:"Tinos",serif;font-size:16px}
.call-box .num{font-family:"Tinos",serif;font-size:26px;font-weight:700;margin-top:6px}
.about-eyebrow{left:663px;top:766px}
.about-title{left:663px;top:794px;font-size:46px;line-height:58px}
.about-rule{left:663px;top:925px}
.about-copy{left:663px;top:952px;width:320px}
.about-copy p{margin-bottom:13px}
.about-btn{left:663px;top:1146px;width:133px;height:50px}

/* services */
.services-bg{left:0;top:1281px;width:1200px;height:726px;background:var(--grey)}
.svc-eyebrow{left:95px;top:1374px}
.svc-title{left:95px;top:1402px;font-size:46px}
.svc-rule{left:95px;top:1489px}
.card{top:1544px;width:319px;height:295px;background:var(--white)}
.card .img{width:100%;height:192px}
.card .name{height:103px;display:flex;align-items:center;justify-content:center;font-family:"Tinos",serif;font-size:22px;color:var(--navy)}
.arrow{top:1664px}
.svc-btn{left:527px;top:1882px;width:131px;height:51px}

/* video */
.video{left:0;top:2007px;width:1200px;height:455px;background:linear-gradient(180deg,#2c2a29 0%,#3b3532 45%,#1f3346 75%,#1c4d6b 100%)}
.play{left:515px;top:2128px;width:160px;height:160px;border:2px solid rgba(255,255,255,.85);border-radius:50%;display:flex;flex-direction:column;align-items:center;justify-content:center;gap:10px;color:var(--white);font-weight:700;font-size:15px}
.video-title{left:0;top:2318px;width:1225px;text-align:center;font-family:"Libre Baskerville",serif;font-size:47px;color:var(--white)}

/* why choose */
.why-bg{left:0;top:2462px;width:1200px;height:560px;background:var(--grey-light)}
.why-eyebrow{left:107px;top:2585px}
.why-title{left:107px;top:2612px;font-size:46px;line-height:60px}
.why-rule{left:107px;top:2752px}
.why-copy{left:107px;top:2766px;width:320px}
.why-btn{left:107px;top:2855px;width:131px;height:50px}
.feature{width:256px;height:159px;background:var(--white)}
.feature svg{position:absolute;left:32px;top:30px}
.feature .f-name{position:absolute;left:32px;top:92px;font-family:"Tinos",serif;font-size:18px;color:#333}
.feature .f-num{position:absolute;right:30px;top:38px;font-family:"Tinos",serif;font-size:80px;line-height:1;color:#e4e4e4}

/* inspired */
.inspired{left:0;top:3022px;width:1200px;height:494px;background:linear-gradient(180deg,#2b3a3c 0%,#3e4a44 40%,#3a5a4f 70%,#2f4a55 100%)}
.insp-title{left:153px;top:3126px;font-size:56px;line-height:66px;color:var(--white)}
.insp-rule{left:153px;top:3273px}
.insp-copy{left:153px;top:3293px;width:320px;color:rgba(255,255,255,.85)}
.insp-btn{left:153px;top:3363px;width:168px;height:50px}
.grey-after{left:0;top:3516px;width:1200px;height:843px;background:var(--grey)}
.quote{left:378px;top:3424px;width:661px;height:269px;background:var(--white)}
.quote p{position:absolute;left:79px;top:56px;width:420px;font-family:"Tinos",serif;font-size:19px;line-height:26.5px;color:#444}
.quote svg{position:absolute;left:515px;top:96px}

/* contact */
.contact-photo{left:151px;top:3778px;width:358px;height:422px;background:linear-gradient(170deg,#3bb3d6 0%,#62c7e0 40%,#c7a57f 70%,#e5e0d8 100%)}
.mail-box{left:238px;top:4095px;width:271px;height:105px;background:var(--navy);color:var(--white);display:flex;align-items:center;padding-left:34px;gap:16px}
.mail-box .lbl{font-size:8px;letter-spacing:.3px;opacity:.75;text-transform:uppercase}
.mail-box .val{font-family:"Tinos",serif;font-size:18px;margin-top:3px}
.ct-eyebrow{left:610px;top:3746px}
.ct-title{left:610px;top:3774px;font-size:46px;line-height:58px}
.ct-rule{left:610px;top:3903px}
.field{background:var(--white);font-size:10px;color:#555;padding:18px 0 0 21px}
.ct-btn{left:896px;top:4218px;width:143px;height:52px}

/* footer */
.footer{left:0;top:4359px;width:1200px;height:389px;background:var(--footer)}
.f-lbl{font-size:9px;font-weight:700;letter-spacing:.3px;color:#a8a8b8;text-transform:uppercase}
.f-val{font-family:"Tinos",serif;font-size:17px;color:var(--white)}
.f-rule{height:2px;width:30px;background:var(--blue)}
.f-brand{color:var(--white)}
.f-input{left:868px;top:4584px;width:177px;height:38px;background:#3b3b50;color:#9a9aac;font-size:11px;display:flex;align-items:center;padding-left:19px}
.f-send{left:1052px;top:4584px;width:48px;height:38px;background:var(--blue);display:flex;align-items:center;justify-content:center}
</style>
</head>
<body>

<!-- hero -->
<div class="abs hero-bg"></div>
<nav class="abs nav">
  <span style="left:339px">HOME</span>
  <span style="left:442px">ABOUT US</span>
  <span style="left:584px">SERVICES</span>
  <span style="left:702px">GALLERY</span>
  <span style="left:827px">OUR TEAM</span>
</nav>
<div class="abs brand" style="left:151px;top:128px">
  <span class="big">MARLOW</span>
  <span class="small">POOL SERVICE</span>
</div>
<h1 class="abs heading hero-title">Making<br>Waves with<br>Excellence</h1>
<p class="abs copy hero-copy">Lorem ipsum dolor sit amet, consectetur adipiscing elit,<br>sed do eiusmod tempor incididunt</p>
<a class="abs btn hero-btn">Learn more</a>
<div class="abs photo hero-photo" role="img" aria-label="Woman relaxing at the edge of a sunlit pool"></div>

<!-- about -->
<div class="abs photo about-photo" role="img" aria-label="Technician with a toolbox working on a pool deck"></div>
<div class="abs call-box">
  <svg width="40" height="40" viewBox="0 0 24 24" fill="none" stroke="#fff" stroke-width="1.3" stroke-linejoin="round"><path d="M5 3h4l2 5-2.5 1.5a11 11 0 0 0 6 6L16 13l5 2v4a2 2 0 0 1-2 2A16 16 0 0 1 3 5a2 2 0 0 1 2-2z"/></svg>
  <div><div class="lbl">For Calls:</div><div class="num">0 800-555-01-42</div></div>
</div>
<div class="abs eyebrow about-eyebrow">About us</div>
<h2 class="abs heading about-title">Crafting Aquatic<br>Masterpieces</h2>
<div class="abs rule about-rule"></div>
<div class="abs copy about-copy">
  <p>Lorem ipsum dolor sit amet, consectetur adipiscing elit,<br>sed do eiusmod tempor incididunt ut labore et dolor<br>e magna aliqua. e magna aliqua. e magna</p>
  <p>Lorem ipsum dolor sit amet, consectetur adipiscing elit,<br>sed do eiusmod tempor incididunt ut labore et dolor<br>e magna aliqua. e magna aliqua. e magna<br>Lorem ipsum dolor sit amet, consectetur adipiscing elit,<br>sed do eiusmod tempor incididunt ut labore et dolor</p>
</div>
<a class="abs btn about-btn">Learn more</a>

<!-- services -->
<div class="abs services-bg"></div>
<div class="abs eyebrow svc-eyebrow">Our services</div>
<h2 class="abs heading svc-title">Services We Provide</h2>
<div class="abs rule svc-rule"></div>
<svg class="abs arrow" style="left:36px" width="42" height="26" viewBox="0 0 42 26" fill="none" stroke="#222" stroke-width="2"><path d="M41 13H2M13 2 2 13l11 11"/></svg>
<svg class="abs arrow" style="left:1124px" width="42" height="26" viewBox="0 0 42 26" fill="none" stroke="#222" stroke-width="2"><path d="M1 13h39M29 2l11 11-11 11"/></svg>
<div class="abs card" style="left:92px">
  <div class="img" role="img" aria-label="Worker scrubbing blue pool tiles" style="background:linear-gradient(135deg,#3a7fb8,#8ab6d6 60%,#c9a27c)"></div>
  <div class="name">Pool Repair</div>
</div>
<div class="abs card" style="left:440px">
  <div class="img" role="img" aria-label="Construction crew in hard hats and safety vests" style="background:linear-gradient(135deg,#c8ccd0,#9aa0a4 50%,#d8dc5a)"></div>
  <div class="name">Pool Construction</div>
</div>
<div class="abs card" style="left:787px">
  <div class="img" role="img" aria-label="Family on a float in a clean pool" style="background:linear-gradient(160deg,#7a8f5a,#5fc3d8 45%,#e27aa0 75%,#b07a52)"></div>
  <div class="name">Pool Cleaning</div>
</div>
<a class="abs btn svc-btn">Learn more</a>

<!-- video -->
<div class="abs video" role="img" aria-label="Modern house with an illuminated pool at dusk"></div>
<div class="abs play">
  <svg width="16" height="18" viewBox="0 0 16 18" fill="none" stroke="#fff" stroke-width="1.5"><path d="M2 2l12 7-12 7z"/></svg>
  <span>Play Video</span>
</div>
<div class="abs video-title">Explanation Video</div>

<!-- why choose -->
<div class="abs why-bg"></div>
<div class="abs eyebrow why-eyebrow">Why choose us</div>
<h2 class="abs heading why-title">Designs That<br>Make a Splash</h2>
<div class="abs rule why-rule"></div>
<p class="abs copy why-copy">Lorem ipsum dolor sit amet, consectetur adipiscing elit,<br>sed do eiusmod tempor incididunt ut labore et dolor<br>e magna aliqua. e magna aliqua. e magna</p>
<a class="abs btn why-btn">Learn more</a>

<div class="abs feature" style="left:581px;top:2582px">
  <svg width="40" height="40" viewBox="0 0 24 24" fill="none" stroke="var(--navy)" stroke-width="1.3"><circle cx="12" cy="12" r="3.2"/><path d="M12 2.5l2 2.3 3-.4.8 2.9 2.7 1.4-1 2.8 1 2.8-2.7 1.4-.8 2.9-3-.4-2 2.3-2-2.3-3 .4-.8-2.9L3.5 14.8l1-2.8-1-2.8 2.7-1.4L7 4.9l3 .4z"/></svg>
  <span class="f-name">Quality Assurance</span><span class="f-num">1</span>
</div>
<div class="abs feature" style="left:842px;top:2582px">
  <svg width="40" height="40" viewBox="0 0 24 24" fill="none" stroke="var(--navy)" stroke-width="1.3"><circle cx="11" cy="11" r="8"/><path d="M3 11h16M11 3c3 3 3 13 0 16M11 3c-3 3-3 13 0 16"/><circle cx="17" cy="17" r="3.5" fill="#fff"/><circle cx="17" cy="17" r="1.2"/></svg>
  <span class="f-name">Professional</span><span class="f-num">2</span>
</div>
<div class="abs feature" style="left:581px;top:2748px">
  <svg width="40" height="40" viewBox="0 0 24 24" fill="none" stroke="var(--navy)" stroke-width="1.3"><circle cx="12" cy="8" r="4"/><path d="M4 21c0-4.4 3.6-7 8-7s8 2.6 8 7z"/></svg>
  <span class="f-name">Experienced</span><span class="f-num">3</span>
</div>
<div class="abs feature" style="left:842px;top:2748px">
  <svg width="40" height="40" viewBox="0 0 24 24" fill="none" stroke="var(--navy)" stroke-width="1.3"><path d="M12 3l8.5 6.2-3.3 10H6.8L3.5 9.2z"/><circle cx="12" cy="3" r="1.3" fill="#fff"/><circle cx="20.5" cy="9.2" r="1.3" fill="#fff"/><circle cx="17.2" cy="19.2" r="1.3" fill="#fff"/><circle cx="6.8" cy="19.2" r="1.3" fill="#fff"/><circle cx="3.5" cy="9.2" r="1.3" fill="#fff"/></svg>
  <span class="f-name">Comprehensive</span><span class="f-num">4</span>
</div>

<!-- inspired -->
<div class="abs inspired" role="img" aria-label="Landscaped backyard pool beside a modern home at twilight"></div>
<div class="abs grey-after"></div>
<h2 class="abs heading insp-title">Inspired Designs,<br>Impeccable Craftsmanship</h2>
<div class="abs rule insp-rule"></div>
<p class="abs copy insp-copy">Lorem ipsum dolor sit amet, consectetur adipiscing elit,<br>sed do eiusmod tempor incididunt ut labore et dolor</p>
<a class="abs btn insp-btn">Go to product page</a>
<div class="abs quote">
  <p>Lorem ipsum dolor sit amet, consectetur ad<br>ipiscing elit, sed do eiusmod tempor incididunt<br>ut labore et dolore magna aliqua. Ut enim ad<br>minim veniam, quis nostrud exercitation<br>ullamco laboris nisi ut aliquip ex ea commodo<br>consequat. Duis aute irure dolor in reprehenderit</p>
  <svg width="102" height="64" viewBox="0 0 102 64" fill="var(--navy)"><path d="M20 0a18 18 0 0 1 18 20c0 22-16 38-32 44l-3-5c10-6 16-15 17-22A18 18 0 0 1 20 0z"/><path d="M82 0a18 18 0 0 1 18 20c0 22-16 38-32 44l-3-5c10-6 16-15 17-22A18 18 0 0 1 82 0z"/></svg>
</div>

<!-- contact -->
<div class="abs photo contact-photo" role="img" aria-label="Woman in a sun hat sitting by a turquoise pool"></div>
<div class="abs mail-box">
  <svg width="42" height="38" viewBox="0 0 24 22" fill="none" stroke="#7fb6ea" stroke-width="1.1"><rect x="2" y="6" width="20" height="14"/><path d="M2 6l10 8 10-8M2 20l7-7M22 20l-7-7M6 6V2h12v4"/></svg>
  <div><div class="lbl">Need to contact us?</div><div class="val">Email Us</div></div>
</div>
<div class="abs eyebrow ct-eyebrow">Contact with us</div>
<h2 class="abs heading ct-title">Any Questions?<br>Let’s Talk!</h2>
<div class="abs rule ct-rule"></div>
<div class="abs field" style="left:606px;top:3953px;width:214px;height:52px">My name is</div>
<div class="abs field" style="left:826px;top:3953px;width:213px;height:52px">My e-mail</div>
<div class="abs field" style="left:606px;top:4012px;width:433px;height:50px">I am interested in:</div>
<div class="abs field" style="left:606px;top:4069px;width:433px;height:133px">My message is:</div>
<a class="abs btn ct-btn">Send a message</a>

<!-- footer -->
<footer class="abs footer"></footer>
<div class="abs f-lbl" style="left:103px;top:4458px">Visit office:</div>
<div class="abs f-val" style="left:103px;top:4476px">48 Harbor Ln. Suite 210</div>
<div class="abs f-rule" style="left:103px;top:4512px"></div>
<div class="abs f-lbl" style="left:103px;top:4531px">Write email:</div>
<div class="abs f-val" style="left:103px;top:4551px">hello@marlowpool.example</div>
<div class="abs f-rule" style="left:103px;top:4587px"></div>
<div class="abs f-lbl" style="left:103px;top:4609px">Make a call:</div>
<div class="abs f-val" style="left:103px;top:4627px">0 (800)-555-01-99</div>

<div class="abs brand f-brand" style="left:455px;top:4500px;align-items:center">
  <span class="big">MARLOW</span>
  <span class="small">POOL SERVICE</span>
</div>
<div class="abs" style="left:475px;top:4630px;width:200px;text-align:center;font-family:'Tinos',serif;font-size:12px;color:#9a9aac">Marlow Pool Service</div>

<div class="abs f-lbl" style="left:868px;top:4485px">Subscribe to our news</div>
<div class="abs f-val" style="left:868px;top:4505px;font-size:16px;line-height:21px">Always Get Our Latets News<br>&amp; Events Newsletter!</div>
<div class="abs f-input">your email</div>
<div class="abs f-send"><svg width="12" height="16" viewBox="0 0 12 16" fill="none" stroke="#fff" stroke-width="2.5"><path d="M3 2l6 6-6 6"/></svg></div>

</body>
</html>
```